Online training business needs new website

We need a new wordpress website as a result of a rebranding. The business is a crisis management training company focussed on online training and simulation exercises. We only need a 4 page site - home, about us, contact us and blog. However we must be able to add additional tabs in the header to redirect to our sales and marketing system (Kartra). As these change from time to time, we must be able to add and delete as required.The site must be editable by us, with a basic understanding of wordpress and no understanding of coding. We don't want to have to employ someone to change text, add posts or add a new workshops etc. The theme chosen must be easy to edit by a beginner.

Target Market(s)

Senior managers food and consumer goods companies

Industry/Entity Type

Consulting

Coding

Coded - Design and coding required

Font styles to use
Sans Serif

Requirements
Must have
• Home page, about us, contact us, blog
• Colour scheme from logo (attached) - maroon, blue and grey
• If you go to the current website "tidewellcollege.com" and click on the "workshops" tab you will see the content I need on the home page for the plumvantage.com site
Nice to have
• Modern, simple and minimalist design is preferred

```html
<!DOCTYPE html>
<html lang="en">
<head>
<meta charset="utf-8">
<title>Contact Us – Plum Vantage</title>
<link href="https://fonts.googleapis.com/css2?family=Roboto:wght@400;500;700&family=Open+Sans:wght@400;700&display=swap" rel="stylesheet">
<style>
  :root{
    --navy:#0b3a6e;
    --maroon:#7e0d3c;
    --grey:#555b63;
    --white:#ffffff;
  }
  *{margin:0;padding:0;box-sizing:border-box}
  html,body{width:839px;height:1200px;overflow:hidden;background:var(--white)}
  body{position:relative;font-family:'Roboto',sans-serif;color:var(--navy)}
  .site-header{position:absolute;top:0;left:0;width:839px;height:78px;background:var(--white);z-index:3}
  .brand{position:absolute;left:118px;top:0;width:118px;height:96px;background:var(--white);border-radius:0 0 60px 60px;display:flex;align-items:center;justify-content:center;gap:6px}
  .brand-dot{width:10px;height:10px;border-radius:50%;background:var(--maroon)}
  .brand-name{font-weight:700;font-size:15px;color:var(--maroon);line-height:1.05;letter-spacing:.5px}
  .main-nav{position:absolute;top:36px;left:261px;display:flex;gap:14px;font-size:12.3px}
  .main-nav a{color:var(--navy);text-decoration:none}
  .main-nav a.current{color:var(--maroon)}
  .hero{position:absolute;top:78px;left:0;width:839px;height:300px;overflow:hidden;background:linear-gradient(135deg,#8a8d91,#5c6066 55%,#a0a3a7)}
  .hero h1{position:absolute;top:108px;width:100%;text-align:center;color:var(--white);font-size:36px;font-weight:700}
  .hero-curve{position:absolute;top:220px;left:0}
  .section-title{position:absolute;top:370px;width:100%;text-align:center;color:var(--maroon);font-size:26px;font-weight:400}
  .contact-card{position:absolute;left:118px;top:446px;font-family:'Open Sans',sans-serif;font-style:normal;font-size:14.5px;color:#333;line-height:25.5px}
  .contact-card h2{font-size:16px;font-weight:700;color:var(--navy);margin-bottom:2px}
  .contact-card .gap{height:9px}
  .map{position:absolute;left:323px;top:442px;width:429px;height:217px;background:linear-gradient(135deg,#ececec,#d6d6d6)}
  .quote-band{position:absolute;top:712px;left:0}
  .quote{position:absolute;top:764px;left:0;width:839px}
  .quote h2{text-align:center;color:var(--white);font-size:22px;font-weight:400;margin-bottom:26px}
  .quote-form{position:relative;width:555px;margin-left:149px;display:grid;grid-template-columns:1fr 1fr;gap:7px 6px}
  .field{height:33px;border:1px solid #c9d3e0;color:var(--white);font-size:11.5px;padding:0 14px;display:flex;align-items:center}
  .field.message{grid-column:1/3;height:86px;align-items:flex-start;padding-top:9px;margin-top:2px}
  .submit{grid-column:1/3;justify-self:center;width:133px;height:36px;border:2px solid var(--white);color:var(--white);font-size:14px;display:flex;align-items:center;justify-content:center;margin-top:5px}
  .site-footer{position:absolute;top:1126px;width:100%;text-align:center}
  .footer-nav{display:flex;justify-content:center;gap:15px;font-size:12px}
  .footer-nav a{color:var(--navy);text-decoration:none}
  .copyright{margin-top:12px;font-size:11.5px;color:var(--grey)}
</style>
</head>
<body>
  <header class="site-header">
    <div class="brand"><span class="brand-dot"></span><span class="brand-name">PLUM<br>VANTAGE</span></div>
    <nav class="main-nav">
      <a href="#">ABOUT US</a><a href="#">WORKSHOPS</a><a href="#">ONLINE COURSE</a><a href="#">SIMULATIONS</a><a href="#" class="current">CONTACT US</a><a href="#">BLOG</a>
    </nav>
  </header>

  <section class="hero" role="img" aria-label="Business people reviewing documents at a desk">
    <h1>CONTACT US</h1>
    <svg class="hero-curve" width="839" height="80" viewBox="0 0 839 80">
      <path d="M0 78 Q420 -2 839 78 L839 80 L0 80 Z" fill="#fff"/>
      <path d="M72 68 Q420 4 767 68" fill="none" stroke="#0b3a6e" stroke-width="3"/>
      <circle cx="420" cy="34" r="26" fill="#fff"/>
    </svg>
  </section>

  <h2 class="section-title">CONTACT</h2>

  <address class="contact-card">
    <h2>PLUM VANTAGE</h2>
    <div>Address:</div>
    <div>14, Reed Court, Westbrook,</div>
    <div>WA 6120</div>
    <div class="gap"></div>
    <div>Phone: 08 5550 2741</div>
    <div>Fax: 08 5550 2742</div>
    <div>Email: info@plumv.com</div>
  </address>

  <div class="map" role="img" aria-label="Street map showing the office location"></div>

  <svg class="quote-band" width="839" height="385" viewBox="0 0 839 385">
    <path d="M0 40 Q420 -25 839 48 L839 330 Q420 420 0 325 Z" fill="#7e0d3c"/>
    <path d="M0 55 Q420 -15 839 50 L839 318 Q420 400 0 330 Z" fill="#0b3a6e"/>
  </svg>

  <section class="quote">
    <h2>REQUEST A QUOTE</h2>
    <div class="quote-form">
      <div class="field">Full Name</div>
      <div class="field">Email address</div>
      <div class="field">Company</div>
      <div class="field">Phone</div>
      <div class="field message">Message</div>
      <div class="submit">SUBMIT</div>
    </div>
  </section>

  <footer class="site-footer">
    <nav class="footer-nav">
      <a href="#">ABOUT US</a><a href="#">WORKSHOPS</a><a href="#">ONLINE COURSE</a><a href="#">SIMULATIONS</a><a href="#">CONTACT US</a><a href="#">BLOG</a>
    </nav>
    <p class="copyright">© 2019 Company Name &nbsp;All right reserved</p>
  </footer>
</body>
</html>
```